Automotive Accessories Business Card

Design a business template that match our new logo design and our industry.

https://www.qelmotorgear.com/

Target Market(s)

Aftermarket auto parts and accessories

Industry/Entity Type

automotive

Contact Information for Business Card

company logo

Font styles to use
Serif
Sans Serif

Colors
EB3D1F
EC4F4E
F09395
F8D3D4
FCEDEE

```html
<!DOCTYPE html>
<html lang="en">
<head>
<meta charset="utf-8">
<title>QEL Motor Gear – Business Card</title>
<link rel="stylesheet" href="https://fonts.googleapis.com/css2?family=Open+Sans:ital,wght@0,400;0,700;0,800;1,700&display=swap">
<style>
  :root {
    --red: #e23a44;
    --ink: #3a3a3c;
    --ink-soft: #555557;
    --band: #333335;
    --card-white: #f4f4f4;
    --card-dark: #3b3b3d;
    --tile-dark: #2c2c2e;
    --stage: #e6e4e1;
    --white: #ffffff;
  }
  * { box-sizing: border-box; margin: 0; padding: 0; }
  html, body {
    width: 1200px; height: 960px; overflow: hidden;
    background: var(--stage);
    font-family: "Open Sans", Arial, sans-serif;
  }
  .stage {
    position: relative; width: 1200px; height: 960px;
  }
  .card {
    position: absolute; left: 320px; width: 560px; height: 320px;
    box-shadow: 0 10px 28px rgba(0,0,0,.18);
    overflow: hidden;
  }
  .card--front {
    top: 110px;
    background: linear-gradient(135deg, var(--white) 0%, var(--card-white) 55%, #e9e9e9 100%);
  }
  .card--back { top: 530px; background: var(--card-dark); }

  /* front */
  .brand {
    position: absolute; left: 140px; top: 38px;
    display: flex; align-items: center; gap: 10px;
  }
  .brand__mark { width: 16px; height: 16px; background: var(--red); }
  .brand__name {
    font-weight: 800; font-size: 30px; letter-spacing: .5px;
    color: var(--ink); text-transform: uppercase;
  }
  .band {
    position: absolute; left: 118px; right: 0; top: 122px; height: 14px;
    background: var(--band);
  }
  .person { position: absolute; left: 44px; top: 150px; }
  .person__name {
    font-weight: 800; font-size: 24px; letter-spacing: 1.5px;
    color: var(--ink); text-transform: uppercase; line-height: 1.1;
  }
  .person__title { font-size: 14px; color: var(--ink-soft); margin-top: 2px; }
  .contacts { position: absolute; left: 30px; top: 222px; list-style: none; }
  .contacts li {
    display: flex; align-items: center; gap: 8px;
    font-size: 14px; color: var(--ink); line-height: 22px;
  }
  .contacts svg { width: 14px; height: 14px; flex: none; }
  .contacts .site-name { color: var(--red); font-weight: 700; font-style: italic; }

  /* back */
  .back__pattern {
    position: absolute; inset: 0;
    background: radial-gradient(ellipse at 40% 35%, #4a4a4c 0%, var(--card-dark) 55%, var(--tile-dark) 100%);
  }
  .back__brand {
    position: absolute; inset: 0;
    display: flex; align-items: center; justify-content: center; gap: 12px;
  }
  .back__brand .brand__mark { width: 20px; height: 20px; background: var(--white); }
  .back__brand .brand__name { color: var(--white); font-size: 38px; }
</style>
</head>
<body>
<main class="stage">
  <section class="card card--front" aria-label="Business card front">
    <div class="brand">
      <span class="brand__mark"></span>
      <span class="brand__name">QEL Motor Gear</span>
    </div>
    <div class="band"></div>
    <div class="person">
      <h1 class="person__name">Marcus Hale</h1>
      <p class="person__title">Sales Manager</p>
    </div>
    <ul class="contacts">
      <li>
        <svg viewBox="0 0 24 24" aria-hidden="true"><path fill="#e23a44" d="M6.6 10.8a15.1 15.1 0 0 0 6.6 6.6l2.2-2.2a1 1 0 0 1 1-.25 11.4 11.4 0 0 0 3.6.57 1 1 0 0 1 1 1V20a1 1 0 0 1-1 1A17 17 0 0 1 3 4a1 1 0 0 1 1-1h3.5a1 1 0 0 1 1 1c0 1.25.2 2.45.57 3.6a1 1 0 0 1-.25 1z"/></svg>
        1-800-555-0142
      </li>
      <li>
        <svg viewBox="0 0 24 24" aria-hidden="true"><path fill="#e23a44" d="M2 5h20v14H2z"/><path fill="none" stroke="#fff" stroke-width="1.6" d="M2 5l10 8 10-8M2 19l7-7M22 19l-7-7"/></svg>
        sales@qelmotorgear.com
      </li>
      <li>
        <svg viewBox="0 0 24 24" aria-hidden="true"><circle cx="12" cy="12" r="10" fill="#e23a44"/><path fill="none" stroke="#fff" stroke-width="1.4" d="M2 12h20M12 2c3 3 3 17 0 20M12 2c-3 3-3 17 0 20"/></svg>
        <span>www.<span class="site-name">qelmotorgear</span>.com</span>
      </li>
    </ul>
  </section>

  <section class="card card--back" aria-label="Business card back">
    <div class="back__pattern" role="img" aria-label="Dark embossed square tile pattern"></div>
    <div class="back__brand">
      <span class="brand__mark"></span>
      <span class="brand__name">QEL Motor Gear</span>
    </div>
  </section>
</main>
</body>
</html>
```